Copperleaf Roofing Business Card

This is my current business card. But I’d like to make some changes. Somewhere on the card I’d like to list some of the services we offer. Maybe on the back? But I’d still like to keep the red. White and black modern look.

-residential & commercial roofing
-Roof Repairs & Maintenance
-Storm Damage & Insurance Claims specialist
-Christmas Lights and permanent Christmas lights
Fencing. Windows. Gutters. Siding. Sheetrock, painting.

```html
<!DOCTYPE html>
<html lang="en">
<head>
<meta charset="utf-8">
<title>Copperleaf Roofing Business Card</title>
<link rel="stylesheet" href="https://fonts.googleapis.com/css2?family=Michroma&family=Open+Sans:wght@400;600&family=Quicksand:wght@500&display=swap">
<style>
  :root {
    --red: #d92027;
    --red-deep: #8c1014;
    --black: #000000;
    --white: #ffffff;
    --page: #ffffff;
  }
  * { box-sizing: border-box; margin: 0; padding: 0; }
  html, body { width: 1100px; height: 1200px; overflow: hidden; background: var(--page); }
  .card {
    position: absolute;
    left: 130px;
    width: 849px;
    height: 464px;
    border-radius: 30px;
    overflow: hidden;
    box-shadow: 0 14px 22px rgba(0,0,0,0.35);
  }
  .card--front { top: 94px; }
  .card--back { top: 651px; background: var(--black); }

  .tartan-fill {
    position: absolute; inset: 0;
    background: linear-gradient(180deg, var(--red-deep) 0%, var(--red) 30%, #5a0a0c 60%, var(--red-deep) 100%);
  }
  .brand-mark {
    position: absolute;
    border-radius: 50%;
    background: var(--red-deep);
    border: 5px solid var(--white);
  }
  .card--front .brand-mark { left: 326px; top: 82px; width: 200px; height: 200px; }
  .brand-name {
    position: absolute;
    font-family: "Michroma", sans-serif;
    color: var(--white);
    text-align: center;
    line-height: 1;
    font-weight: 400;
  }
  .card--front .brand-name { left: 0; right: 0; top: 306px; }
  .brand-name__main { display: block; font-size: 44px; letter-spacing: 1px; }
  .brand-name__sub { display: block; font-size: 30px; margin-top: 18px; }

  .person { position: absolute; left: 38px; top: 62px; width: 410px; text-align: right; }
  .person__name {
    font-family: "Michroma", sans-serif;
    font-size: 34px;
    line-height: 1;
    color: var(--white);
    white-space: nowrap;
  }
  .person__name .first { color: var(--red); }
  .person__role {
    font-family: "Open Sans", sans-serif;
    font-size: 25px;
    color: var(--white);
    margin-top: 14px;
  }
  .person__role .accent { color: var(--red); }

  .services {
    position: absolute; left: 29px; top: 262px;
    list-style: none;
    font-family: "Quicksand", sans-serif;
    font-weight: 500;
    font-size: 16px;
    line-height: 26.5px;
    color: var(--white);
  }
  .divider { position: absolute; left: 486px; top: 207px; width: 1.5px; height: 195px; background: var(--white); }

  .card--back .brand-mark { left: 608px; top: 14px; width: 114px; height: 114px; border-width: 4px; }
  .card--back .brand-name { left: 540px; width: 250px; top: 178px; }
  .card--back .brand-name__main { font-size: 21px; letter-spacing: 0; }
  .card--back .brand-name__sub { font-size: 16px; margin-top: 10px; }

  .contact { position: absolute; left: 540px; top: 256px; list-style: none; font-family: "Open Sans", sans-serif; font-size: 19px; color: var(--white); }
  .contact li { display: flex; align-items: center; height: 32px; gap: 8px; }
  .contact svg { width: 20px; height: 20px; flex: none; }
  .contact .phone { letter-spacing: 3px; }

  .tartan-band {
    position: absolute; left: 0; right: 0; bottom: 0; height: 20px;
    background: linear-gradient(90deg, var(--red-deep), var(--red) 50%, var(--red-deep));
  }
</style>
</head>
<body>
  <section class="card card--front">
    <div class="tartan-fill" role="img" aria-label="Red, black and white tartan plaid pattern"></div>
    <div class="brand-mark"></div>
    <div class="brand-name">
      <span class="brand-name__main">COPPERLEAF</span>
      <span class="brand-name__sub">ROOFING CO.</span>
    </div>
  </section>

  <section class="card card--back">
    <div class="person">
      <h1 class="person__name"><span class="first">DALE</span> MERCER</h1>
      <p class="person__role">Roofing contractor in <span class="accent">Texas</span></p>
    </div>

    <ul class="services">
      <li>-residential &amp; commercial roofing</li>
      <li>-Roof Repairs &amp; Maintenance</li>
      <li>-Storm Damage &amp; Insurance Claims specialist</li>
      <li>-Christmas Lights and permanent Christmas lights</li>
      <li>Fencing. Windows. Gutters. Siding. Sheetrock, painting.</li>
    </ul>

    <div class="divider"></div>

    <div class="brand-mark"></div>
    <div class="brand-name">
      <span class="brand-name__main">COPPERLEAF</span>
      <span class="brand-name__sub">ROOFING CO.</span>
    </div>

    <ul class="contact">
      <li>
        <svg viewBox="0 0 24 24" aria-hidden="true"><path fill="#d92027" d="M6.6 10.8a15.1 15.1 0 0 0 6.6 6.6l2.2-2.2c.3-.3.7-.4 1-.2 1.1.4 2.3.6 3.6.6.6 0 1 .4 1 1V20c0 .6-.4 1-1 1A17 17 0 0 1 3 4c0-.6.4-1 1-1h3.5c.6 0 1 .4 1 1 0 1.3.2 2.5.6 3.6.1.3 0 .7-.2 1z"/></svg>
        <span class="phone">682-555-0148</span>
      </li>
      <li>
        <svg viewBox="0 0 24 24" aria-hidden="true"><rect x="2" y="5" width="20" height="14" fill="#d92027"/><path d="M2 5l10 8 10-8" fill="none" stroke="#000" stroke-width="1.5"/></svg>
        <span>dale@copperleafroofing.co</span>
      </li>
      <li>
        <svg viewBox="0 0 24 24" aria-hidden="true"><g fill="none" stroke="#d92027" stroke-width="1.8"><circle cx="12" cy="12" r="9"/><ellipse cx="12" cy="12" rx="4" ry="9"/><path d="M3 12h18M5 7h14M5 17h14"/></g></svg>
        <span>www.copperleafroofing.co</span>
      </li>
    </ul>

    <div class="tartan-band" role="img" aria-label="Strip of red and black tartan plaid"></div>
  </section>
</body>
</html>
```